Brightline Energy Product Distribution Brochure

We are looking to have our current brochure for our customers completely redesigned...the idea is to present the relevant information in an attractive way . Our website is brightlineenergyco.example where you can find more information about us. We have included a file with a rough idea of the page order and what each should include but feel free to adapt based on design. The example provided is only for context and doesnt have to be maintained. We will be using the brochure both digitally and in print form. As long as it reads easily and is eye catching, the design can be horizontal or vertical.Final deliverable should be indesign file.

"Our Brands" page: should be limited to one page (space being enough) where it has the header for each one (for example diesel generators) space for one or two lines of text and then the corresponding logos for each of the five categories
Updates

For those asking: the "our brands" page should be a single page layout where there is a header with the corresponding section and space for maybe one line of text followed by the two logos for that category. Each of the product pages should be similar in fashion to the one in the document attached: a photo of the product with some white space and space for the text to be included. We will be posting additional examples today

Target Market(s)

We want to present it to customers both digitally and in print so they can see our products

Industry/Entity Type

Power Generation

Font styles to use
Serif

Requirements
Must have
• Eye catching and able to present the information in a presentable fashion. Rest is up to you.
Nice to have
• Should incorporate the colors of our logo but can also add other depending on design

```html
<!DOCTYPE html>
<html lang="en">
<head>
<meta charset="utf-8">
<title>Brightline Energy — Catalogue Cover</title>
<link href="https://fonts.googleapis.com/css2?family=Lato:wght@400;700&display=swap" rel="stylesheet">
<style>
  :root {
    --canvas: #e9e9e9;
    --charcoal: #3c3b3d;
    --yellow: #f6dc1f;
    --yellow-deep: #f3c425;
    --amber: #e9ad22;
    --amber-light: #f1bb29;
    --white: #ffffff;
    --ink: #1d1d1b;
    --brand-grey: #5a5a5c;
  }
  html, body {
    margin: 0;
    width: 1200px;
    height: 1200px;
    overflow: hidden;
    background: var(--canvas);
    font-family: "Lato", Arial, sans-serif;
  }
  .cover {
    position: absolute;
    left: 59px;
    top: 33px;
    width: 1079px;
    height: 762px;
    background: var(--charcoal);
    box-shadow: 0 2px 6px rgba(0,0,0,0.18);
    overflow: hidden;
  }
  .cover-photo {
    position: absolute;
    left: 0; top: 0;
    width: 1079px;
    height: 444px;
    background:
      radial-gradient(ellipse 380px 200px at 340px 230px, #7f9bb3 0%, rgba(127,155,179,0.55) 45%, rgba(0,0,0,0) 100%),
      radial-gradient(ellipse 200px 140px at 720px 260px, #f1c11e 0%, rgba(241,193,30,0.5) 50%, rgba(0,0,0,0) 100%),
      radial-gradient(ellipse 200px 220px at 960px 200px, #8a7a45 0%, rgba(138,122,69,0.3) 55%, rgba(0,0,0,0) 100%),
      linear-gradient(180deg, #2f5a80 0%, #2a3f55 45%, #0d0f12 78%, #141516 100%);
  }
  .cover-shapes {
    position: absolute;
    left: 0; top: 0;
    width: 1079px;
    height: 762px;
  }
  .tagline {
    position: absolute;
    left: 62px;
    top: 465px;
    margin: 0;
    font-size: 18.5px;
    font-weight: 700;
    color: var(--ink);
    letter-spacing: -0.2px;
  }
  .brand {
    position: absolute;
    left: 68px;
    top: 662px;
    display: flex;
    align-items: center;
    gap: 14px;
  }
  .brand-mark {
    width: 34px;
    height: 34px;
    background: var(--amber-light);
  }
  .brand-name {
    font-size: 26px;
    font-weight: 400;
    color: var(--brand-grey);
    letter-spacing: 1px;
  }
</style>
</head>
<body>
  <section class="cover">
    <div class="cover-photo" role="img" aria-label="Photo of an open-frame diesel generator set beside a yellow canopied generator, with a lit refinery at dusk behind"></div>

    <svg class="cover-shapes" viewBox="0 0 1079 762" aria-hidden="true">
      <defs>
        <linearGradient id="yellowFade" x1="0" y1="0" x2="1" y2="0">
          <stop offset="0" stop-color="#f5e21e"/>
          <stop offset="1" stop-color="#f4c823"/>
        </linearGradient>
      </defs>
      <polygon class="band-yellow" points="0,444 802,444 848,515 650,762 541,762 410,515 0,515" fill="url(#yellowFade)"/>
      <polygon class="panel-white" points="0,515 410,515 541,762 0,762" fill="var(--white)"/>
      <polygon class="tri-amber-light" points="595,762 735,540 870,762" fill="var(--amber-light)"/>
      <polygon class="tri-amber" points="730,518 1045,518 868,762" fill="var(--amber)" opacity="0.95"/>
    </svg>

    <p class="tagline">The Highest quality brands and products for the power generation industry</p>

    <div class="brand">
      <span class="brand-mark"></span>
      <span class="brand-name">Brightline Energy</span>
    </div>
  </section>
</body>
</html>
```